Boutique custom software development company needs new business card

Our nearly 20 year old custom software development company would like to better include the fact that we are now providing Bitcoin services. These new services are B2B include education (how to acquire and securely hold Bitcoin) and integrating Bitcoin payments into existing ecommerce sites or other existing systems. Please keep the card clean and simple. Attached is our current design and some other files. vextorial.com

Target Market(s)

businesses owners interested in long term relationship

Industry/Entity Type

Custom software development and Bitcoin

Contact Information for Business Card

Dale Parker, dale@vextorial.com, vextorial.com, (888) 555-VXTRL

Font styles to use
Other font styles liked:
• monospace

Requirements
Must have
• double-sided
Nice to have
• clean and simple
Should not have
• physical address

```html
<!DOCTYPE html>
<html lang="en">
<head>
<meta charset="utf-8">
<title>Vextorial Business Card</title>
<link href="https://fonts.googleapis.com/css2?family=Montserrat:wght@500;600;700&family=Lato:wght@400&display=swap" rel="stylesheet">
<style>
  :root {
    --bg: #cbcbcb;
    --paper: #f7f7f7;
    --orange: #ef7d24;
    --blue: #3a6fbb;
    --blue-deep: #2f5fa8;
    --blue-light: #4a80c9;
    --ink: #1d1d1f;
    --white: #ffffff;
  }
  * { box-sizing: border-box; margin: 0; padding: 0; }
  html, body { width: 1200px; height: 1036px; overflow: hidden; }
  body {
    background: var(--bg);
    font-family: "Montserrat", sans-serif;
    position: relative;
  }
  .card {
    position: absolute;
    left: 180px;
    width: 840px;
    height: 480px;
    overflow: hidden;
    box-shadow: 0 10px 30px rgba(0,0,0,0.18);
  }
  .card-front { top: 28px; background: var(--paper); }
  .card-back { top: 528px; }

  /* front */
  .front-band {
    position: absolute; left: 0; right: 0; bottom: 0; height: 200px;
    background: var(--orange);
  }
  .front-square {
    position: absolute; right: -40px; top: 230px; width: 260px; height: 220px;
    background: var(--blue);
  }
  .contact-block { position: absolute; left: 96px; top: 62px; }
  .contact-name {
    color: var(--orange); font-weight: 600; font-size: 30px;
    letter-spacing: 0.5px; text-transform: uppercase; margin-bottom: 18px;
  }
  .contact-list { list-style: none; }
  .contact-item {
    display: flex; align-items: center; gap: 12px;
    font-weight: 600; font-size: 22px; color: var(--ink);
    line-height: 34px;
  }
  .contact-icon { width: 20px; height: 20px; flex: none; }
  .services {
    position: absolute; left: 96px; top: 318px;
    list-style: none;
    color: var(--white); font-weight: 600; font-size: 21px; line-height: 31px;
  }
  .brand { position: absolute; text-align: left; }
  .brand-front { right: 70px; top: 92px; }
  .brand-name {
    display: block; font-family: "Montserrat", sans-serif; font-weight: 700;
    font-size: 52px; line-height: 1; letter-spacing: -0.5px;
  }
  .brand-front .brand-name { color: var(--blue); }
  .brand-tagline {
    display: block; font-family: "Lato", sans-serif; font-size: 16px; margin-top: 4px;
  }
  .brand-front .brand-tagline { color: var(--blue); }

  /* back */
  .back-pattern {
    position: absolute; inset: 0;
    background: linear-gradient(120deg, var(--blue-deep) 0%, var(--blue) 50%, var(--blue-light) 100%);
  }
  .brand-back { left: 50%; top: 50%; transform: translate(-50%, -50%); }
  .brand-back .brand-name { color: var(--white); font-size: 58px; }
  .brand-back .brand-tagline { color: var(--white); font-size: 17px; }
</style>
</head>
<body>

<section class="card card-front">
  <div class="front-band"></div>
  <div class="front-square"></div>

  <div class="contact-block">
    <h1 class="contact-name">Dale Parker</h1>
    <ul class="contact-list">
      <li class="contact-item">
        <svg class="contact-icon" viewBox="0 0 24 24"><path fill="var(--blue)" d="M6.6 10.8a15 15 0 0 0 6.6 6.6l2.2-2.2c.3-.3.7-.4 1-.2 1.1.4 2.3.6 3.6.6.6 0 1 .4 1 1V20c0 .6-.4 1-1 1A17 17 0 0 1 3 4c0-.6.4-1 1-1h3.5c.6 0 1 .4 1 1 0 1.3.2 2.5.6 3.6.1.3 0 .7-.2 1z"/></svg>
        (888) 555-VXTRL
      </li>
      <li class="contact-item">
        <svg class="contact-icon" viewBox="0 0 24 24"><rect x="6" y="2" width="12" height="20" rx="2" fill="none" stroke="var(--blue)" stroke-width="2"/><circle cx="12" cy="18" r="1.2" fill="var(--blue)"/></svg>
        502.555.0187
      </li>
      <li class="contact-item">
        <svg class="contact-icon" viewBox="0 0 24 24"><rect x="2" y="5" width="20" height="14" fill="var(--blue)"/><path d="M2 5l10 8 10-8" fill="none" stroke="var(--white)" stroke-width="1.6"/></svg>
        dale@vextorial.com
      </li>
      <li class="contact-item">
        <svg class="contact-icon" viewBox="0 0 24 24"><g fill="none" stroke="var(--blue)" stroke-width="1.8"><circle cx="12" cy="12" r="9"/><ellipse cx="12" cy="12" rx="4" ry="9"/><path d="M3 12h18M5 7h14M5 17h14"/></g></svg>
        www.vextorial.com
      </li>
    </ul>
  </div>

  <ul class="services">
    <li>Custom Software Development</li>
    <li>Bitcoin Education</li>
    <li>Bitcoin Payment Integration</li>
  </ul>

  <div class="brand brand-front">
    <span class="brand-name">Vextorial</span>
    <span class="brand-tagline">developer of custom applications</span>
  </div>
</section>

<section class="card card-back">
  <div class="back-pattern" role="img" aria-label="Repeating faint company wordmark pattern in tones of blue"></div>
  <div class="brand brand-back">
    <span class="brand-name">Vextorial</span>
    <span class="brand-tagline">developer of custom applications</span>
  </div>
</section>

</body>
</html>
```